Coastline Premier Retreats Business Card Design

Design a business card for Coastline Premier Retreats. Look at the website for colors and reference. Card should have logo, name, title, office number, mobile number, email, URL and a tagline like, "Luxury Hotel & Resort Email Marketing" (This might change).

https://www.coastlinepremierretreats.example

The rest I will leave up to your imagination.

Contact Information for Business Card

Logo, name, title, office number, mobile number, email, URL and a tagline like, "Luxury Hotel & Resort Email Marketing" (This might change).

```html
<!DOCTYPE html>
<html lang="en">
<head>
<meta charset="utf-8">
<title>Coastline Premier Retreats – Business Card</title>
<link href="https://fonts.googleapis.com/css2?family=Montserrat:wght@400;500;700;800&display=swap" rel="stylesheet">
<style>
  :root{
    --bg:#262628;
    --card-dark:#2c2c30;
    --card-dark-emboss:#232326;
    --card-light:#ffffff;
    --ink:#151515;
    --accent:#f07a20;
    --muted:#333;
  }
  *{box-sizing:border-box;margin:0;padding:0}
  html,body{width:1200px;height:900px;overflow:hidden;background:var(--bg);font-family:"Montserrat",sans-serif}
  .stage{position:relative;width:1200px;height:900px}
  .card{
    position:absolute;width:520px;height:297px;border-radius:18px;overflow:hidden;
    box-shadow:0 18px 40px rgba(0,0,0,.45);
  }
  .card::after{content:"";position:absolute;left:0;right:0;bottom:0;height:7px;background:var(--accent)}
  .card--back{left:50px;top:302px;background:var(--card-dark)}
  .card--front{left:630px;top:302px;background:var(--card-light)}

  .wordmark{display:flex;align-items:center;gap:12px;font-weight:800;letter-spacing:.04em;text-transform:uppercase}
  .wordmark__square{width:16px;height:16px;background:currentColor;flex:none}

  .card--back .wordmark{position:absolute;left:0;right:0;top:100px;justify-content:center;color:var(--card-dark-emboss);font-size:27px;text-shadow:0 1px 0 rgba(255,255,255,.05)}
  .tagline{position:absolute;left:0;right:0;top:196px;text-align:center;color:var(--accent);font-weight:700;font-size:14px;letter-spacing:.01em}

  .card--front .wordmark{position:absolute;left:40px;top:40px;color:var(--ink);font-size:24px}
  .contact-block{position:absolute;left:40px;top:112px;display:flex;align-items:center;gap:18px}
  .person{text-align:right}
  .person__name{color:var(--accent);font-weight:700;font-size:20px}
  .person__title{color:var(--muted);font-size:12px;font-weight:500}
  .divider{width:2px;height:86px;background:var(--accent)}
  .contact-list{list-style:none;display:flex;flex-direction:column;gap:6px;font-size:11.5px;color:var(--ink)}
  .contact-list li{display:flex;align-items:center;gap:8px}
  .contact-list svg{width:12px;height:12px;flex:none}
  .address{position:absolute;left:0;right:0;bottom:38px;text-align:center;font-size:12px;color:var(--ink)}
</style>
</head>
<body>
<main class="stage">
  <section class="card card--back" aria-label="Card back">
    <div class="wordmark"><span class="wordmark__square"></span>Coastline Premier Retreats</div>
    <p class="tagline">Luxury Hotel &amp; Resort Email Marketing</p>
  </section>

  <section class="card card--front" aria-label="Card front">
    <div class="wordmark"><span class="wordmark__square" style="color:var(--accent)"></span>Coastline Premier Retreats</div>
    <div class="contact-block">
      <div class="person">
        <p class="person__name">Daniel Verano</p>
        <p class="person__title">Owner</p>
      </div>
      <span class="divider"></span>
      <ul class="contact-list">
        <li><svg viewBox="0 0 24 24" fill="var(--accent)"><path d="M6.6 10.8a15 15 0 0 0 6.6 6.6l2.2-2.2a1 1 0 0 1 1-.25 11.4 11.4 0 0 0 3.6.57 1 1 0 0 1 1 1V20a1 1 0 0 1-1 1A17 17 0 0 1 3 4a1 1 0 0 1 1-1h3.5a1 1 0 0 1 1 1c0 1.25.2 2.45.57 3.57a1 1 0 0 1-.25 1z"/></svg>555.210.4318 x 112</li>
        <li><svg viewBox="0 0 24 24" fill="none" stroke="var(--accent)" stroke-width="2.4"><rect x="6" y="2" width="12" height="20" rx="2"/><line x1="11" y1="18" x2="13" y2="18"/></svg>555.864.2097</li>
        <li><svg viewBox="0 0 24 24" fill="var(--accent)"><path d="M2 5h20v14H2z"/><path d="M2 5l10 8 10-8" fill="none" stroke="#fff" stroke-width="1.8"/></svg>info@coastlinepremierretreats.example</li>
        <li><svg viewBox="0 0 24 24" fill="none" stroke="var(--accent)" stroke-width="2.2"><circle cx="12" cy="12" r="9"/><path d="M3 12h18M12 3c3 3 3 15 0 18M12 3c-3 3-3 15 0 18"/></svg>www.coastlinepremierretreats.example</li>
      </ul>
    </div>
    <p class="address">418 Harbor Way, Suite 210 Bayview, CA 90000</p>
  </section>
</main>
</body>
</html>
```